Media Services Start-up -- Corporate Website and Logo Design. Inspiration required!

We need a logo design and corporate website design, including coding, for our start-up business.
Vennatra’s value proposition is based on bringing together media content from a vast number of geographies globally, adding human and AI curation, translation and editing, and delivering the content using tailored customer interfaces. On the one hand, the business brings together media coverage from all over the world, and on the other it brings together content, human skills and technology to deliver a supreme customer experience.
Vennatra is a B2B media monitoring and analytics business with emphasis on global customers. Vennatra's service offering is centred around sourcing media content from different markets, processing, storing and delivering the content and insights derived from it using an online platform / mobile app.
The messaging we want to create through the logo is:
- Global scope
- Speed of delivery
- Cost-efficiency
- Multi-lingual
- Tailor-made
- Trustworthy
Target Market(s)
Business to business, PR / Communications, Media, Marketing
Logo Text
Vennatra
Coding
Coded - Design and coding required
Number of Pages Required
5+ page
Font styles to use
Other font styles liked:
- See Design Brief for details
Colors
Designer to choose colors to be used in the design.

```html
<!DOCTYPE html>
<html lang="en">
<head>
<meta charset="utf-8">
<title>Vennatra Media Intelligence – Our Technology</title>
<link href="https://fonts.googleapis.com/css2?family=Roboto:wght@400;500;700&display=swap" rel="stylesheet">
<style>
  :root {
    --teal: #3bb3a0;
    --header-bg: #151515;
    --page-bg: #1c1c1c;
    --text: #ffffff;
    --muted: #d9d9d9;
  }
  * { margin: 0; padding: 0; box-sizing: border-box; }
  html, body { width: 1200px; height: 490px; overflow: hidden; background: var(--page-bg); }
  body { font-family: "Roboto", sans-serif; color: var(--text); position: relative; }

  .hero-visual {
    position: absolute; inset: 85px 0 35px 0;
    background:
      radial-gradient(circle at 600px 210px, #3a3a3a 0, #262626 140px, #1a1a1a 320px, #141414 600px),
      #161616;
  }

  .site-header {
    position: absolute; top: 0; left: 0; width: 1200px; height: 85px;
    background: var(--header-bg);
  }
  .brand {
    position: absolute; left: 141px; top: 26px;
    display: flex; align-items: center; gap: 10px;
    font-size: 20px; font-weight: 500; letter-spacing: .5px;
  }
  .brand-square { width: 22px; height: 22px; background: var(--teal); }

  .contact-bar {
    position: absolute; top: 11px; right: 143px;
    display: flex; gap: 26px; font-size: 14px;
  }
  .contact-item { display: flex; align-items: center; gap: 9px; }
  .contact-icon { width: 27px; height: 27px; }

  .main-nav {
    position: absolute; top: 49px; right: 141px;
    display: flex; align-items: center; gap: 26px; font-size: 14.5px;
  }
  .main-nav a { color: var(--text); text-decoration: none; }
  .main-nav a.is-active { color: var(--teal); font-weight: 500; }
  .main-nav .sign-in {
    background: var(--teal); padding: 0 15px; height: 28px; line-height: 28px;
    font-size: 15px; letter-spacing: .5px; margin-left: -7px;
  }

  .technology {
    position: absolute; top: 85px; left: 0; width: 1200px; height: 370px;
  }
  .technology h1 {
    position: absolute; top: 50px; width: 100%; text-align: center;
    font-size: 32px; font-weight: 700;
  }
  .technology .lead {
    position: absolute; top: 108px; width: 100%; text-align: center;
    font-size: 14px; font-weight: 700; line-height: 23px;
  }
  .feature-list {
    position: absolute; top: 184px; left: 141px; width: 870px; list-style: none;
  }
  .feature-list li {
    position: relative; padding-left: 30px; font-size: 14px; line-height: 23px;
    color: var(--muted); margin-bottom: 11px;
  }
  .feature-list svg { position: absolute; left: 0; top: 3px; width: 15px; height: 15px; }

  .site-footer {
    position: absolute; bottom: 0; left: 0; width: 1200px; height: 35px;
    background: var(--teal); font-size: 13px;
  }
  .site-footer .copyright { position: absolute; left: 141px; top: 9px; }
  .social { position: absolute; right: 143px; top: 10px; display: flex; gap: 10px; }
  .social span { width: 14px; height: 14px; border-radius: 50%; background: var(--text); }
</style>
</head>
<body>
  <div class="hero-visual" role="img" aria-label="Dark city skyline at night with a glowing globe, network lines and circular technology icons"></div>

  <header class="site-header">
    <div class="brand"><span class="brand-square"></span>Vennatra</div>

    <div class="contact-bar">
      <div class="contact-item">
        <svg class="contact-icon" viewBox="0 0 28 28" aria-hidden="true">
          <circle cx="14" cy="14" r="13" fill="none" stroke="#fff" stroke-width="1.2"/>
          <path d="M10 8.5c.6-.5 1.3-.4 1.7.2l1.1 1.7c.3.5.2 1.1-.2 1.4l-.8.6c.6 1.4 1.7 2.6 3.1 3.2l.6-.8c.4-.4 1-.5 1.4-.2l1.7 1.1c.6.4.7 1.2.2 1.7l-.9.9c-3.5.6-8.5-4.4-7.9-7.9z" fill="#fff"/>
        </svg>
        +1 555 010 2040
      </div>
      <div class="contact-item">
        <svg class="contact-icon" viewBox="0 0 28 28" aria-hidden="true">
          <circle cx="14" cy="14" r="13" fill="none" stroke="#fff" stroke-width="1.2"/>
          <rect x="8" y="10" width="12" height="8.5" fill="#fff"/>
          <path d="M8 10l6 5 6-5M8 18.5l4.5-4M20 18.5l-4.5-4" fill="none" stroke="#151515" stroke-width="1"/>
        </svg>
        hello@vennatra.net
      </div>
    </div>

    <nav class="main-nav">
      <a href="#" class="is-active">Home</a>
      <a href="#">Solutions</a>
      <a href="#">Our Approach</a>
      <a href="#">Our People</a>
      <a href="#">Our Technology</a>
      <a href="#" class="sign-in">SIGN IN</a>
    </nav>
  </header>

  <main class="technology">
    <h1>Our Technology</h1>
    <p class="lead">At the core of our systems is the knowledge of the latest Cloud-based technologies,<br>providing excellent business continuity and efficiencies.</p>
    <ul class="feature-list">
      <li><svg viewBox="0 0 16 16" aria-hidden="true"><rect x="1" y="1" width="14" height="14" rx="3" fill="none" stroke="#3bb3a0" stroke-width="2"/><path d="M4.5 8.2l2.4 2.3 4.6-4.9" fill="none" stroke="#3bb3a0" stroke-width="1.8"/></svg>We have developed our own technology to fulfil end- to-end customer requirements.</li>
      <li><svg viewBox="0 0 16 16" aria-hidden="true"><rect x="1" y="1" width="14" height="14" rx="3" fill="none" stroke="#3bb3a0" stroke-width="2"/><path d="M4.5 8.2l2.4 2.3 4.6-4.9" fill="none" stroke="#3bb3a0" stroke-width="1.8"/></svg>Our technology suite consists of intgestion system, data stores, editorial tools, delivery system.</li>
      <li><svg viewBox="0 0 16 16" aria-hidden="true"><rect x="1" y="1" width="14" height="14" rx="3" fill="none" stroke="#3bb3a0" stroke-width="2"/><path d="M4.5 8.2l2.4 2.3 4.6-4.9" fill="none" stroke="#3bb3a0" stroke-width="1.8"/></svg>We place great emphasis on tailoring our solutions to customer needs by creating custom media platforms, customised email and coverage templates, and enabling customers to edit and manipulate content.</li>
    </ul>
  </main>

  <footer class="site-footer">
    <p class="copyright">Copyright © 2019 Vennatra Media Intelligence. All Rights Reserved.</p>
    <div class="social" aria-label="Social links"><span></span><span></span><span></span></div>
  </footer>
</body>
</html>
```